Swing Dance Themed Cleaning Company Website

We need a website designed for a cleaning company based in Portland, Oregon called Foxtrot Lane. We clean homes and commercial buildings, inside and out.

needs to be vintage and like the velvet tambour. Speakeasy 1920s feel.
needs to be classy.

Check out foxtrotlane.com We are not happy with the site currently.

please look at house scout site for more content https://www.housescoutpro.com/rated.FoxtrotLaneCleaning.48217705.html

Check out my videos on my ClipHaven channel Foxtrot Lane

Target Market(s)

middle class and home owner

Industry/Entity Type

Cleaning Service

Number of Pages Required

3 page

Font styles to use
Other font styles liked:
• jazzrag

Colors

Designer to choose colors to be used in the design.

Requirements
Must have
• must be good on pc and mobile

```html
<!DOCTYPE html>
<html lang="en">
<head>
<meta charset="utf-8">
<title>Foxtrot Lane — Keep Cleaning Classy Portland</title>
<link rel="stylesheet" href="https://fonts.googleapis.com/css2?family=Poiret+One&family=Nunito+Sans:ital,wght@0,300;0,400;0,600;1,300;1,400&display=swap">
<style>
  :root {
    --gold: #e2a40c;
    --gold-bright: #f9c21f;
    --gold-deep: #d99d00;
    --ink: #3a3a3a;
    --text: #555555;
    --footer: #333333;
    --paper: #ffffff;
    --frame: #efeeea;
  }
  * { margin: 0; padding: 0; box-sizing: border-box; }
  html, body { width: 1200px; height: 2250px; overflow: hidden; }
  body {
    position: relative;
    background: var(--paper);
    font-family: "Nunito Sans", Arial, sans-serif;
    color: var(--text);
  }
  .deco { font-family: "Poiret One", "Century Gothic", sans-serif; font-weight: 400; }

  /* Header */
  .site-header {
    position: absolute; top: 0; left: 0; width: 1200px; height: 120px;
    background: linear-gradient(#eef0f3, rgba(255,255,255,0.6));
  }
  .brand { position: absolute; left: 78px; top: 24px; }
  .brand-name {
    font-family: "Nunito Sans", Arial, sans-serif; font-weight: 600;
    font-size: 30px; line-height: 34px; color: var(--gold); text-transform: uppercase;
    letter-spacing: 1px;
  }
  .brand-tagline {
    margin-top: 14px; font-size: 11px; font-weight: 600; color: var(--gold);
    letter-spacing: 0.5px;
  }
  .main-nav { position: absolute; top: 52px; right: 78px; display: flex; gap: 38px; }
  .main-nav a {
    font-size: 15px; color: var(--ink); text-decoration: none; letter-spacing: 0.5px;
  }
  .main-nav a.is-current { color: var(--gold); }

  /* Hero slider */
  .hero-frame {
    position: absolute; left: 78px; top: 115px; width: 1044px; height: 530px;
    background: var(--frame);
    box-shadow: 0 5px 6px rgba(0,0,0,0.3);
  }
  .hero-image {
    position: absolute; left: 8px; top: 15px; width: 1028px; height: 438px;
    border-radius: 6px;
    background: linear-gradient(100deg, #c9b8a2 0%, #a48a6c 35%, #7d6148 62%, #5b4634 100%);
  }
  .hero-title {
    position: absolute; left: 118px; top: 280px; font-size: 62px; line-height: 72px;
    color: var(--gold-bright); text-transform: uppercase; font-weight: 400;
    text-shadow: 2px 3px 2px rgba(0,0,0,0.55);
  }
  .slider-dots { position: absolute; left: 0; right: 0; top: 477px; display: flex; justify-content: center; gap: 22px; }
  .slider-dots span { width: 20px; height: 20px; border-radius: 50%; background: #2f2f2f; }
  .slider-dots span.is-active { background: var(--gold); }

  /* About */
  .about { position: absolute; top: 705px; left: 0; width: 1200px; text-align: center; }
  .section-title { font-size: 44px; color: var(--gold); text-transform: uppercase; line-height: 52px; }
  .about-lead { margin-top: 12px; font-style: italic; font-size: 17px; color: var(--text); }
  .about-sub { margin-top: 12px; font-size: 25px; color: var(--gold); text-transform: uppercase; font-weight: 400; }
  .about-text { width: 800px; margin: 14px auto 0; font-size: 14.5px; line-height: 25px; }
  .actions { margin-top: 28px; display: flex; justify-content: center; gap: 11px; }
  .btn {
    width: 188px; height: 48px; border-radius: 24px; font-size: 20px;
    display: flex; align-items: center; justify-content: center; text-transform: uppercase;
    border: 2px solid var(--gold);
  }
  .btn-solid { background: var(--gold); color: #2b2b2b; }
  .btn-outline { background: var(--paper); color: var(--gold); }

  /* Services */
  .services { position: absolute; top: 1068px; left: 0; width: 1200px; height: 580px; }
  .services-band { position: absolute; inset: 0; }
  .services-inner { position: absolute; inset: 0; text-align: center; color: #fff; }
  .services .section-title { color: #fff; margin-top: 83px; }
  .services-intro { width: 680px; margin: 14px auto 0; font-size: 14.5px; line-height: 25px; }
  .service-list { position: absolute; top: 238px; left: 0; width: 1200px; }
  .service { position: absolute; width: 240px; text-align: center; }
  .service-icon {
    width: 114px; height: 114px; margin: 0 auto; border: 2px solid #fff; border-radius: 50%;
    display: flex; align-items: center; justify-content: center;
  }
  .service-name { margin-top: 26px; font-size: 22px; font-weight: 600; }
  .service-desc { margin-top: 6px; font-size: 14px; line-height: 25px; }

  /* Contact */
  .reach-out { position: absolute; top: 1692px; left: 0; width: 1200px; text-align: center; }
  .reach-text { width: 720px; margin: 14px auto 0; font-size: 14.5px; line-height: 25px; }
  .reach-cta { margin-top: 14px; font-size: 14.5px; }
  .contact-row { position: absolute; top: 1918px; left: 0; width: 1200px; height: 140px; }
  .contact-links { position: absolute; left: 0; top: 0; }
  .contact-item { position: absolute; top: 0; width: 240px; text-align: center; }
  .contact-icon {
    width: 56px; height: 56px; margin: 0 auto; border-radius: 50%; background: #fff;
    border: 2px solid #444; box-shadow: 2px 3px 5px rgba(0,0,0,0.3);
    display: flex; align-items: center; justify-content: center;
  }
  .contact-label { margin-top: 22px; font-size: 14.5px; line-height: 25px; color: var(--text); }

  /* Footer */
  .site-footer {
    position: absolute; top: 2104px; left: 0; width: 1200px; height: 146px;
    background: var(--footer); text-align: center;
  }
  .social { display: flex; justify-content: center; gap: 7px; margin-top: 30px; }
  .social span { width: 42px; height: 42px; border: 2px solid #fff; border-radius: 50%; }
  .copyright { margin-top: 22px; color: #fff; font-size: 14px; }
</style>
</head>
<body>

<header class="site-header">
  <div class="brand">
    <div class="brand-name">Foxtrot Lane</div>
    <div class="brand-tagline">KEEP CLEANING CLASSY PORTLAND</div>
  </div>
  <nav class="main-nav">
    <a class="is-current" href="#">HOME</a>
    <a href="#">ABOUT</a>
    <a href="#">SERVICES</a>
    <a href="#">BLOG</a>
    <a href="#">CONTACT</a>
  </nav>
</header>

<section class="hero-frame">
  <div class="hero-image" role="img" aria-label="Photo of a smiling vintage-styled housekeeper in a green striped dress holding a duster and spray bottle, in front of a softly blurred bright living room"></div>
  <h1 class="hero-title deco">Keep Cleaning<br>Classy Portland</h1>
  <div class="slider-dots"><span class="is-active"></span><span></span><span></span></div>
</section>

<section class="about">
  <h2 class="section-title deco">About Us</h2>
  <p class="about-lead">Making the greater Portland area clean, one building at a time</p>
  <h3 class="about-sub deco">Good People, Great Service</h3>
  <p class="about-text">Foxtrot Lane is a family owned professional cleaning business. We provide our years of cleaning experience to homes and businesses in and around Portland, Oregon. If you need something cleaned, have it cleaned the right way — contact us. Any doubts you have will be wiped away by our fantastic service and personable employees.</p>
  <div class="actions">
    <span class="btn btn-solid deco">Leave a Review</span>
    <span class="btn btn-outline deco">Leave a Review</span>
  </div>
</section>

<section class="services">
  <svg class="services-band" width="1200" height="580" viewBox="0 0 1200 580" preserveAspectRatio="none" aria-hidden="true">
    <defs>
      <radialGradient id="bandGlow" cx="0.5" cy="0.4" r="0.7">
        <stop offset="0" stop-color="#fcc21d"/>
        <stop offset="1" stop-color="#dc9f00"/>
      </radialGradient>
    </defs>
    <path fill="url(#bandGlow)" d="M0 16 L40 14 L80 18 L120 12 L170 15 L220 10 L270 13 L330 9 L380 12 L430 8 L480 11 L540 6 L600 10 L640 4 L700 9 L760 5 L820 8 L880 3 L940 7 L1000 2 L1060 6 L1110 0 L1160 4 L1200 1
      L1200 566 L1160 570 L1110 566 L1060 572 L1000 568 L940 574 L880 569 L820 575 L760 570 L700 576 L640 571 L580 577 L520 572 L460 578 L400 573 L340 579 L280 574 L220 580 L160 575 L100 580 L50 576 L0 580 Z"/>
  </svg>
  <div class="services-inner">
    <h2 class="section-title deco">Our Services</h2>
    <p class="services-intro">We provide cleaning and janitorial services for one-time and recurring needs. While this isn't an exhaustive list of available services, these are certainly the most commonly requested!</p>
    <div class="service-list">
      <div class="service" style="left:76px">
        <div class="service-icon">
          <svg width="48" height="48" viewBox="0 0 48 48" fill="none" stroke="#fff" stroke-width="2"><path d="M14 4v22M8 26h12l2 18H6z"/><path d="M34 4v18M28 22h12v6H28zM30 28c0 8-6 10-6 16M38 28c0 8 6 10 6 16"/></svg>
        </div>
        <div class="service-name">Janitorial Services</div>
        <div class="service-desc">Routine janitorial, Tall cleaning, Food service sanitation, Clean room services</div>
      </div>
      <div class="service" style="left:342px">
        <div class="service-icon">
          <svg width="52" height="48" viewBox="0 0 52 48" fill="none" stroke="#fff" stroke-width="2"><path d="M6 22L26 6l20 16M10 19v23h32V19"/><rect x="21" y="28" width="10" height="14"/><circle cx="12" cy="10" r="2"/><circle cx="40" cy="30" r="3"/></svg>
        </div>
        <div class="service-name">House-cleaning</div>
        <div class="service-desc">Floors, Carpet cleaning, Refuse removal, Dusting, Interior windows, Blinds</div>
      </div>
      <div class="service" style="left:613px">
        <div class="service-icon">
          <svg width="48" height="48" viewBox="0 0 48 48" fill="none" stroke="#fff" stroke-width="2"><path d="M8 40L30 18M30 18c-3-8 4-14 10-12l-6 6 2 4 4 2 6-6c2 6-4 13-12 10"/><path d="M40 40L18 18M12 6l6 6-4 4-6-6z"/></svg>
        </div>
        <div class="service-name">Maintenance</div>
        <div class="service-desc">Pressure washing, Gutters, Painting, Exterior windows, Construction cleanup, Detailing</div>
      </div>
      <div class="service" style="left:884px">
        <div class="service-icon">
          <svg width="46" height="46" viewBox="0 0 46 46" fill="none" stroke="#fff" stroke-width="2"><rect x="5" y="8" width="36" height="33" rx="3"/><path d="M5 16h36M14 4v8M32 4v8"/><circle cx="23" cy="29" r="7"/><path d="M19.5 29l2.5 2.5 4.5-5"/></svg>
        </div>
        <div class="service-name">Event services</div>
        <div class="service-desc">Event hosting at the elm street studio Event cleanup</div>
      </div>
    </div>
  </div>
</section>

<section class="reach-out">
  <h2 class="section-title deco">Reach Out</h2>
  <p class="reach-text">We have a flexible team ready to meet your cleaning needs, servicing Multnomah, Washington, and Clackamas Counties. Offering cleaning, janitorial, and maintenance services for your home, apartment or business, we provide both one-time as well as weekly, bi-weekly or monthly cleaning services.</p>
  <p class="reach-cta">If you're ready to experience a professional cleaning, reach out to us now!</p>
</section>

<div class="contact-row">
  <svg class="contact-links" width="1200" height="60" viewBox="0 0 1200 60" aria-hidden="true">
    <g stroke="#cccccc" stroke-width="3" fill="none">
      <path d="M418 22H582M500 34H600"/>
      <path d="M632 22H714M632 34H797"/>
    </g>
    <g stroke="#e2a40c" stroke-width="2" fill="#fff">
      <circle cx="418" cy="22" r="4"/><circle cx="500" cy="34" r="4"/>
      <circle cx="714" cy="22" r="4"/><circle cx="797" cy="34" r="4"/>
    </g>
  </svg>
  <div class="contact-item" style="left:217px">
    <div class="contact-icon">
      <svg width="18" height="22" viewBox="0 0 18 22"><path fill="#e2a40c" d="M9 0a8 8 0 0 0-8 8c0 6 8 14 8 14s8-8 8-14a8 8 0 0 0-8-8zm0 11a3 3 0 1 1 0-6 3 3 0 0 1 0 6z"/></svg>
    </div>
    <div class="contact-label">418 SE Birch Ave #210, Portland,<br>OR 97215</div>
  </div>
  <div class="contact-item" style="left:487px">
    <div class="contact-icon">
      <svg width="20" height="20" viewBox="0 0 20 20"><path fill="#e2a40c" d="M4 1l3 0 2 5-2 2c1 2 3 4 5 5l2-2 5 2v3c0 1-1 3-3 3C8 19 1 12 1 4c0-2 2-3 3-3z"/></svg>
    </div>
    <div class="contact-label">971-555-0148</div>
  </div>
  <div class="contact-item" style="left:757px">
    <div class="contact-icon">
      <svg width="20" height="16" viewBox="0 0 20 16" fill="none" stroke="#e2a40c" stroke-width="2"><rect x="1" y="1" width="18" height="14" rx="1"/><path d="M1 2l9 7 9-7"/></svg>
    </div>
    <div class="contact-label">hello@foxtrotlane.com</div>
  </div>
</div>

<footer class="site-footer">
  <div class="social" aria-label="Social media links">
    <span aria-label="Social link 1"></span>
    <span aria-label="Social link 2"></span>
    <span aria-label="Social link 3"></span>
    <span aria-label="Social link 4"></span>
    <span aria-label="ClipHaven channel"></span>
  </div>
  <p class="copyright">©FOXTROT LANE– 2018. All Rights Reserved.</p>
</footer>

</body>
</html>
```